Business Card for Inovative Flexible Packaging Company

Create a business card that is both simple and stricking at the same time.
Preferably only one color (orange) or two colors (black and orange).
Information to print:
Lumtrex, Lda
[T] 22 418 6095
[M] 91 362 7148
[F] 22 418 6037
[@] lumtrex.ac@mailvora.com
SEDE & ARMAZÉM
Rua Das Figueiras do Monte, 317
Serzedo
4415-238 Serzedo - VN Gaia
PORTUGAL
Reason: A lot of the ideas are obvious. I want something different. Inovative. dare to do something eye catching with style.
Target Market(s)
Business Consumers. Packaging Designers.
Industry/Entity Type
Business
Look and feel
Each slider illustrates characteristics of the customer's brand and the style your logo design should communicate.

```html
<!DOCTYPE html>
<html lang="pt">
<head>
<meta charset="utf-8">
<title>Lumtrex, Lda — Cartão de Visita</title>
<link rel="stylesheet" href="https://fonts.googleapis.com/css2?family=Roboto:wght@400;500&display=swap">
<style>
  :root {
    --orange: #f15a29;
    --black: #0a0a0a;
    --band: #111111;
    --white: #ffffff;
    --ink: #222222;
    --stage: #d9d9d9;
  }
  * { margin: 0; padding: 0; box-sizing: border-box; }
  html, body { width: 1200px; height: 804px; overflow: hidden; }
  body {
    position: relative;
    background: var(--stage);
    font-family: "Roboto", Arial, sans-serif;
  }

  .card { position: absolute; overflow: hidden; background: var(--white); width: 600px; height: 343px; }

  /* Front */
  .card-front { left: 40px; top: 30px; }
  .card-front .top-field {
    position: absolute; left: 0; top: 0; width: 100%; height: 196px;
    background: var(--black);
  }
  .card-front .brand-square {
    position: absolute; left: 33px; top: 115px; width: 190px; height: 190px;
    background: var(--orange);
  }
  .card-front .brand-name {
    position: absolute; left: 252px; top: 214px;
    font-size: 66px; font-weight: 500; line-height: 1;
    color: var(--ink);
  }

  /* Back */
  .card-back { left: 560px; top: 430px; }
  .card-back .brand-square {
    position: absolute; left: 30px; top: 34px; width: 44px; height: 44px;
    background: var(--orange);
  }
  .card-back .brand-name {
    position: absolute; left: 86px; top: 30px;
    font-size: 48px; font-weight: 500; line-height: 1;
    color: var(--ink);
  }
  .card-back .address {
    position: absolute; right: 16px; top: 44px; width: 250px;
    font-size: 11px; line-height: 14px; text-align: center; color: var(--ink);
    font-style: normal;
  }
  .card-back .accent-rule {
    position: absolute; left: 0; top: 200px; width: 100%; height: 2px;
    background: var(--orange);
  }
  .card-back .contact-band {
    position: absolute; left: 0; top: 203px; width: 100%; height: 140px;
    background: repeating-linear-gradient(90deg, #141414 0 2px, #0c0c0c 2px 4px);
    color: var(--white);
  }
  .company {
    position: absolute; left: 30px; top: 4px;
    font-size: 26px; font-weight: 400;
  }
  .contact {
    position: absolute; display: flex; align-items: center; gap: 12px;
    font-size: 15px;
  }
  .contact svg { width: 30px; height: 30px; flex: none; }
  .contact.phone { left: 28px; top: 46px; }
  .contact.mobile { left: 28px; top: 92px; }
  .contact.fax { right: 28px; top: 46px; }
  .contact.email { right: 28px; top: 92px; }
</style>
</head>
<body>

<section class="card card-front">
  <div class="top-field"></div>
  <div class="brand-square"></div>
  <div class="brand-name">Lumtrex</div>
</section>

<section class="card card-back">
  <div class="brand-square"></div>
  <div class="brand-name">Lumtrex</div>

  <address class="address">
    SEDE &amp; ARMAZÉM<br>
    Rua Das Figueiras do Monte, 317 Serzedo<br>
    4415-238 Serzedo - VN Gaia PORTUGAL
  </address>

  <div class="accent-rule"></div>

  <div class="contact-band">
    <div class="company">Lumtrex, Lda</div>

    <div class="contact phone">
      <svg viewBox="0 0 40 40" aria-hidden="true">
        <path d="M9 5 l6 0 l3 8 l-4 3 c2 5 5 8 10 10 l3 -4 l8 3 l0 6 c0 2 -2 4 -4 4 C17 35 5 23 5 9 c0 -2 2 -4 4 -4z" fill="var(--orange)"/>
        <path d="M24 5 a11 11 0 0 1 11 11 M24 10 a6 6 0 0 1 6 6" stroke="var(--orange)" stroke-width="2.5" fill="none"/>
      </svg>
      <span>22 418 6095</span>
    </div>

    <div class="contact mobile">
      <svg viewBox="0 0 40 40" aria-hidden="true">
        <rect x="11" y="3" width="18" height="34" rx="3" fill="var(--orange)"/>
        <rect x="14" y="7" width="12" height="10" fill="var(--band)"/>
        <g fill="var(--band)">
          <rect x="14" y="21" width="3" height="3"/><rect x="19" y="21" width="3" height="3"/><rect x="24" y="21" width="2" height="3"/>
          <rect x="14" y="26" width="3" height="3"/><rect x="19" y="26" width="3" height="3"/><rect x="24" y="26" width="2" height="3"/>
          <rect x="14" y="31" width="3" height="3"/><rect x="19" y="31" width="3" height="3"/><rect x="24" y="31" width="2" height="3"/>
        </g>
      </svg>
      <span>91 362 7148</span>
    </div>

    <div class="contact fax">
      <span>22 418 6037</span>
      <svg viewBox="0 0 40 40" aria-hidden="true">
        <rect x="4" y="14" width="32" height="22" rx="2" fill="none" stroke="var(--orange)" stroke-width="2.5"/>
        <rect x="11" y="3" width="18" height="14" fill="none" stroke="var(--orange)" stroke-width="2.5"/>
        <rect x="9" y="24" width="22" height="8" fill="var(--orange)"/>
      </svg>
    </div>

    <div class="contact email">
      <span>lumtrex.ac@mailvora.com</span>
      <svg viewBox="0 0 40 40" aria-hidden="true">
        <rect x="3" y="9" width="34" height="23" fill="none" stroke="var(--orange)" stroke-width="2.5"/>
        <path d="M3 9 L20 23 L37 9 M3 32 L15 19 M37 32 L25 19" fill="none" stroke="var(--orange)" stroke-width="2.5"/>
      </svg>
    </div>
  </div>
</section>

</body>
</html>
```